Healthy Meal Delivery Website needs a new face lift

Hi there,

The current website i have is super old and outdated.

I would like a beautiful modern site that has all the same content as the previous except with a a new, modern and trustworthy feel.

The current website is http://www.larkibite.ca/

Target Market(s)

Diet Meal delivery, weight loss, healthy meal delivery

Industry/Entity Type

Food Service

Number of Pages Required

5+ page

Font styles to use
Sans Serif

Requirements
Must have
• Modern & Clean
Should not have
• Anything outdated or cheesy

```html
<!DOCTYPE html>
<html lang="en">
<head>
<meta charset="utf-8">
<title>Larkibite Delivery – Fresh Diet Meals</title>
<link rel="stylesheet" href="https://fonts.googleapis.com/css2?family=Roboto+Condensed:wght@400;700&family=Open+Sans:ital,wght@0,400;0,600;0,700;1,700&display=swap">
<style>
:root{
  --blue:#2a7cc0;
  --blue-deep:#1660a6;
  --green:#4aa843;
  --red:#e3161f;
  --ink:#222;
  --muted:#6b6b6b;
  --grey-bg:#eeeeee;
  --footer:#000;
  --accordion:#d6edf7;
  --accordion-line:#9fd0e8;
  --white:#fff;
}
*{margin:0;padding:0;box-sizing:border-box}
html,body{width:1200px;height:3766px;overflow:hidden;background:var(--white)}
body{position:relative;font-family:"Open Sans",sans-serif;color:var(--ink)}
.abs{position:absolute}
.heading{font-family:"Roboto Condensed",sans-serif;font-weight:400}

/* header */
.top-line{left:0;top:0;width:1200px;height:6px;background:var(--blue)}
.brand{left:90px;top:40px;display:flex;align-items:center;gap:12px}
.brand-dot{width:34px;height:34px;border-radius:50%;background:var(--blue)}
.brand-name{font-family:"Roboto Condensed",sans-serif;font-weight:700;font-size:36px;color:var(--blue);line-height:1}
.tagline{left:360px;top:50px;width:460px;text-align:center;font-weight:700;font-style:italic;line-height:1.3}
.tagline .t1{font-size:18px;color:#1f8fd6}
.tagline .t2{font-size:16px;color:var(--ink)}
.phone{left:905px;top:36px;display:flex;align-items:center;gap:10px;font-size:20px}
.socials{left:917px;top:75px;display:flex;gap:12px}
.socials span{width:27px;height:27px;border-radius:50%}

/* nav */
.nav{left:0;top:148px;width:1200px;height:52px;background:var(--blue);display:flex;padding-left:90px}
.nav a{color:var(--white);text-decoration:none;font-size:15px;line-height:52px;padding:0 24px}
.nav a.active{background:var(--green)}

/* hero */
.hero{left:0;top:200px;width:1200px;height:580px;background:linear-gradient(100deg,#b9a995 0%,#e9e2d6 30%,#d8d2c4 55%,#7d8b5a 80%,#4f5e35 100%)}
.hero-title{left:0;top:418px;width:1200px;text-align:center;color:var(--white);font-family:"Roboto Condensed",sans-serif;font-weight:700;font-size:58px;text-shadow:0 2px 6px rgba(0,0,0,.35)}
.hero-sub{left:0;top:500px;width:1200px;text-align:center;color:var(--white);font-family:"Roboto Condensed",sans-serif;font-size:31px;text-shadow:0 2px 5px rgba(0,0,0,.35)}
.btn{display:inline-block;color:var(--white);text-align:center;border-radius:20px}
.btn-red{background:var(--red)}
.btn-green{background:var(--green)}
.hero-btn{left:525px;top:570px;width:152px;height:40px;line-height:40px;font-size:19px;font-family:"Roboto Condensed",sans-serif}
.hero-arrows{left:1063px;top:703px;display:flex;gap:4px}
.hero-arrows span{width:20px;height:20px;border-radius:50%;background:rgba(0,0,0,.6)}

/* intro */
.intro-title{left:0;top:892px;width:1200px;text-align:center;font-size:35px}
.intro-text{left:110px;top:955px;width:980px;text-align:center;font-size:13.5px;line-height:1.9}
.intro-frame{left:125px;top:1047px;width:390px;height:262px;border:2px solid #999;background:var(--white)}
.intro-photo{left:147px;top:1063px;width:385px;height:262px;background:linear-gradient(135deg,#d9cfbd,#b8a488 55%,#3e6b55);box-shadow:0 3px 8px rgba(0,0,0,.25)}
.benefits{left:563px;top:1080px;list-style:none;font-size:15px}
.benefits li{display:flex;align-items:center;gap:10px;height:33px}
.benefits svg{flex:none}

/* program */
.program{left:0;top:1430px;width:1200px;height:680px}
.program-title{left:0;top:1512px;width:1200px;text-align:center;color:var(--white);font-size:33px}
.card{top:1612px;width:314px;height:385px;background:var(--white);box-shadow:0 2px 6px rgba(0,0,0,.25)}
.card-img{height:195px}
.card h3{font-size:16px;font-weight:600;text-align:center;margin-top:28px}
.card p{font-size:12.5px;line-height:1.7;text-align:center;margin:14px 28px 0;height:64px;overflow:hidden}
.card .btn{display:block;margin:14px auto 0;width:108px;height:32px;line-height:32px;font-size:13px}

/* delivery */
.delivery-title{left:95px;top:2238px;font-size:33px}
.acc{left:95px;width:542px;background:var(--accordion);border:2px solid var(--accordion-line);font-size:14px;padding:0 18px;color:#333}
.acc.open{background:var(--white);border-color:#ccc}
.acc .row{display:flex;justify-content:space-between;align-items:center;height:58px}
.acc.open .row{height:42px}
.acc p{font-size:11.5px;line-height:1.7;color:#555}
.acc .sq{width:14px;height:14px;background:#a9d3ea;border:1px solid #7fb9da}
.acc.open .sq{background:#ccc;border-color:#aaa}
.delivery-photo{left:668px;top:2295px;width:445px;height:337px;background:linear-gradient(160deg,#5a4436,#8c6a4c 40%,#3a2b22 75%,#c8782b);box-shadow:0 3px 8px rgba(0,0,0,.3)}
.dp-title{left:668px;top:2420px;width:445px;text-align:center;color:var(--white);font-family:"Roboto Condensed",sans-serif;font-weight:700;font-size:29px}
.dp-sub{left:668px;top:2463px;width:445px;text-align:center;color:var(--white);font-family:"Roboto Condensed",sans-serif;font-size:16px}
.dp-btn{left:827px;top:2560px;width:126px;height:32px;line-height:32px;font-size:15px;font-family:"Roboto Condensed",sans-serif}

/* testimonials */
.testi-bg{left:0;top:2770px;width:1200px;height:520px;background:var(--grey-bg)}
.testi-title{left:0;top:2830px;width:1200px;text-align:center;font-size:35px}
.quote{top:2947px;width:452px;height:225px;background:var(--white);border:2px solid #ddd;box-shadow:0 3px 8px rgba(0,0,0,.25);padding:52px 25px 0 108px}
.quote h4{font-size:17px;font-weight:400;color:#333}
.quote p{font-size:13px;line-height:1.75;color:#8a8a8a;margin-top:8px;width:260px;text-align:justify}
.quote .who{text-align:right;color:var(--blue);font-size:16px;margin-top:10px;padding-right:35px}
.quote .mark{position:absolute;right:28px;top:28px}
.avatar{width:124px;height:124px;border-radius:50%;border:4px solid var(--white);box-shadow:0 2px 6px rgba(0,0,0,.3)}

/* footer */
.footer{left:0;top:3270px;width:1200px;height:496px;background:var(--footer)}
.fcol{top:3392px;color:var(--white)}
.fcol h5{font-family:"Roboto Condensed",sans-serif;font-weight:400;font-size:21px;margin-bottom:20px}
.fcol ul{list-style:none;font-size:14px;line-height:31px}
.fcontact{display:flex;gap:12px;margin-bottom:26px}
.fcontact b{display:block;font-size:14px;font-weight:600}
.fcontact span{font-size:13px}
.field{display:block;width:315px;height:35px;background:var(--white);margin-bottom:10px;padding-left:16px;line-height:35px;font-size:14px;color:#333}
.send{width:127px;height:36px;background:var(--blue);color:var(--white);text-align:center;line-height:36px;font-size:15px;margin-top:10px}
.fdivider{left:90px;top:3685px;width:1020px;height:1px;background:#444}
.copy{left:0;top:3705px;width:1200px;text-align:center;color:#ccc;font-size:13px}
</style>
</head>
<body>

<div class="abs top-line"></div>

<header>
  <div class="abs brand"><span class="brand-dot"></span><span class="brand-name">Larkibite Delivery</span></div>
  <div class="abs tagline"><div class="t1">Fresh Customized Diet Meals Delivered Daily</div><div class="t2">Toronto and Canada wide</div></div>
  <div class="abs phone">
    <svg width="18" height="18" viewBox="0 0 24 24"><path fill="#222" d="M6.6 10.8a15 15 0 0 0 6.6 6.6l2.2-2.2c.3-.3.7-.4 1-.2 1.1.4 2.3.6 3.6.6.6 0 1 .4 1 1V20c0 .6-.4 1-1 1A17 17 0 0 1 3 4c0-.6.4-1 1-1h3.5c.6 0 1 .4 1 1 0 1.3.2 2.5.6 3.6.1.3 0 .7-.2 1z"/></svg>
    <span>TEL: 416-555-0142</span>
  </div>
  <div class="abs socials" aria-label="Social links">
    <span style="background:#3b5998"></span><span style="background:#8a3ab9"></span><span style="background:#d62020"></span><span style="background:#1da1f2"></span><span style="background:#2a6bb0"></span>
  </div>
</header>

<nav class="abs nav">
  <a class="active">Home</a><a>How It Works</a><a>Pricing</a><a>Sample Menu</a><a>Celebrity</a><a>F.A.Q.</a><a>Contact</a><a>Sign Up</a><a>Customer Login</a>
</nav>

<section>
  <div class="abs hero" role="img" aria-label="Photo of a smiling woman eating a fresh salad at a table with juices and vegetables"></div>
  <svg class="abs" style="left:0;top:720px" width="1200" height="62" viewBox="0 0 1200 62"><path d="M0 40 C300 10 500 0 700 25 C900 50 1050 30 1200 10 V62 H0Z" fill="#fff"/></svg>
  <div class="abs hero-title">Fresh diet meals delivered</div>
  <div class="abs hero-sub">Providing Toronto diet meal delivery for 15 years</div>
  <span class="abs btn btn-red hero-btn">Order Now</span>
  <div class="abs hero-arrows"><span></span><span></span></div>
</section>

<section>
  <h1 class="abs heading intro-title">FRESH DIET GOURMET MEALS DELIVERED by the Larkibite</h1>
  <p class="abs intro-text">Fresh diet meal delivery Toronto and Canada wide is our signature fresh gourmet diet meal delivery program designed for healthy living &amp; weight loss management.Diet meal delivery Toronto has a creative gourmet menu that uses exotic flavors and ingredients to enhance your dining experience.</p>
  <div class="abs intro-frame"></div>
  <div class="abs intro-photo" role="img" aria-label="Photo of a woman measuring her waist with a tape measure"></div>
  <ul class="abs benefits">
    <li><svg width="14" height="14" viewBox="0 0 14 14"><circle cx="7" cy="7" r="7" fill="#1d4f80"/><path d="M5.5 4l3 3-3 3" stroke="#fff" stroke-width="1.6" fill="none"/></svg>BENEFITS - Fresh diet meal delivery daily</li>
    <li><svg width="14" height="14" viewBox="0 0 14 14"><circle cx="7" cy="7" r="7" fill="#1d4f80"/><path d="M5.5 4l3 3-3 3" stroke="#fff" stroke-width="1.6" fill="none"/></svg>MENU - Inspired fresh gourmet Larkibite Diet meals</li>
    <li><svg width="14" height="14" viewBox="0 0 14 14"><circle cx="7" cy="7" r="7" fill="#1d4f80"/><path d="M5.5 4l3 3-3 3" stroke="#fff" stroke-width="1.6" fill="none"/></svg>VARIETY - 60 Day Menu Rotation</li>
    <li><svg width="14" height="14" viewBox="0 0 14 14"><circle cx="7" cy="7" r="7" fill="#1d4f80"/><path d="M5.5 4l3 3-3 3" stroke="#fff" stroke-width="1.6" fill="none"/></svg>CUSTOMIZATION - Every fresh Larkibite Diet meal is personally customized</li>
    <li><svg width="14" height="14" viewBox="0 0 14 14"><circle cx="7" cy="7" r="7" fill="#1d4f80"/><path d="M5.5 4l3 3-3 3" stroke="#fff" stroke-width="1.6" fill="none"/></svg>DELIVERY - Fresh diet meal delivery daily Toronto and Canada wide</li>
    <li><svg width="14" height="14" viewBox="0 0 14 14"><circle cx="7" cy="7" r="7" fill="#1d4f80"/><path d="M5.5 4l3 3-3 3" stroke="#fff" stroke-width="1.6" fill="none"/></svg>CUSTOMER SERVICE - Personal Nutritionist available 7 days a week</li>
  </ul>
</section>

<section>
  <svg class="abs program" viewBox="0 0 1200 680" preserveAspectRatio="none" role="img" aria-label="Blue band with a soft photo of fresh vegetables">
    <defs><linearGradient id="blueBand" x1="0" y1="0" x2="1" y2="1"><stop offset="0" stop-color="#1a6cb5"/><stop offset=".5" stop-color="#2b7fc4"/><stop offset="1" stop-color="#155a9e"/></linearGradient></defs>
    <path d="M0 45 C250 0 450 10 650 30 C850 50 1000 0 1200 15 V640 C1000 600 800 680 600 665 C400 650 200 600 0 640Z" fill="url(#blueBand)"/>
  </svg>
  <h2 class="abs heading program-title">PROGRAM DETAILS</h2>
  <div class="abs card" style="left:108px">
    <div class="card-img" role="img" aria-label="Photo of grilled chicken with herbs" style="background:linear-gradient(135deg,#6b2a14,#b3441f 50%,#3b1a0e)"></div>
    <h3>Enjoy our gourmet menu</h3>
    <p>Every fresh diet meal delivered is prepared with the finest ingredients available and has a creative menu that uses unique and</p>
    <span class="btn btn-green">Order Now</span>
  </div>
  <div class="abs card" style="left:445px">
    <div class="card-img" role="img" aria-label="Photo of a smiling woman in a white shirt" style="background:linear-gradient(135deg,#e8e4de,#c9bdb0 50%,#6c7f86)"></div>
    <h3>Customized for you</h3>
    <p>Every fresh diet meal delivered is prepared with the finest ingredients available and has a creative menu that uses unique and</p>
    <span class="btn btn-green">Order Now</span>
  </div>
  <div class="abs card" style="left:785px">
    <div class="card-img" role="img" aria-label="Photo of a fresh vegetable wrap" style="background:linear-gradient(135deg,#7a6a55,#d8c29a 45%,#8c3a2a 70%,#5d7a3a)"></div>
    <h3>pause your program anytime</h3>
    <p>Every fresh diet meal delivered is prepared with the finest ingredients available and has a creative menu that uses unique and</p>
    <span class="btn btn-green">Order Now</span>
  </div>
</section>

<section>
  <h2 class="abs heading delivery-title">Delivery System</h2>
  <div class="abs acc open" style="top:2297px;height:96px">
    <div class="row"><span>WHAT'S IN YOUR BAG?</span><span class="sq"></span></div>
    <p>Your daily temperature controlled cooler will have all of your meals so you won't need to supplement with any additional snacks or produce during the day.</p>
  </div>
  <div class="abs acc" style="top:2422px"><div class="row"><span>YOUR DAILY MENU</span><span class="sq"></span></div></div>
  <div class="abs acc" style="top:2493px"><div class="row"><span>RECYCLABLE CONTAINERS</span><span class="sq"></span></div></div>
  <div class="abs acc" style="top:2565px"><div class="row"><span>RETURNING YOUR COOLER</span><span class="sq"></span></div></div>
  <div class="abs delivery-photo" role="img" aria-label="Photo of a grilled fish plate with lentils and carrots"></div>
  <div class="abs dp-title">Fresh diet meals delivered</div>
  <div class="abs dp-sub">Providing Toronto diet meal delivery for 15 years.</div>
  <span class="abs btn btn-red dp-btn">Order Now</span>
</section>

<section>
  <svg class="abs" style="left:0;top:2740px" width="1200" height="60" viewBox="0 0 1200 60"><path d="M0 30 C300 60 600 0 900 20 C1050 30 1130 35 1200 30 V60 H0Z" fill="#eeeeee"/></svg>
  <div class="abs testi-bg"></div>
  <h2 class="abs heading testi-title">Testimonials</h2>
  <div class="abs quote" style="left:150px">
    <svg class="mark" width="50" height="36" viewBox="0 0 50 36"><path d="M0 36V20C0 8 6 2 18 0v7c-6 2-8 6-8 11h8v18zM28 36V20C28 8 34 2 46 0v7c-6 2-8 6-8 11h8v18z" fill="#4aa843"/></svg>
    <h4>Neque porro quisquam</h4>
    <p>The point of using Lorem Ipsum is that it has a more-or-less normal distribution of letters, as opposed to using 'Content</p>
    <div class="who">-&nbsp;&nbsp; Helen</div>
  </div>
  <div class="abs avatar" style="left:113px;top:2998px;background:linear-gradient(135deg,#b0302c,#4a2018)" role="img" aria-label="Customer portrait"></div>
  <div class="abs quote" style="left:670px">
    <svg class="mark" width="50" height="36" viewBox="0 0 50 36"><path d="M0 36V20C0 8 6 2 18 0v7c-6 2-8 6-8 11h8v18zM28 36V20C28 8 34 2 46 0v7c-6 2-8 6-8 11h8v18z" fill="#4aa843"/></svg>
    <h4>Dolorem ipsum quia dolor</h4>
    <p>The point of using Lorem Ipsum is that it has a more-or-less normal distribution of letters, as opposed to using 'Content</p>
    <div class="who">- Amet</div>
  </div>
  <div class="abs avatar" style="left:633px;top:2998px;background:linear-gradient(135deg,#d9b68a,#8a6a4a)" role="img" aria-label="Customer portrait"></div>
</section>

<footer>
  <svg class="abs" style="left:0;top:3240px" width="1200" height="40" viewBox="0 0 1200 40"><path d="M0 30 C400 0 800 0 1200 25 V40 H0Z" fill="#000"/></svg>
  <div class="abs footer"></div>
  <div class="abs fcol" style="left:90px">
    <h5>CONTACT US</h5>
    <div class="fcontact"><svg width="20" height="16" viewBox="0 0 20 16"><rect x="1" y="1" width="18" height="14" fill="none" stroke="#fff" stroke-width="1.5"/><path d="M1 1l9 7 9-7" fill="none" stroke="#fff" stroke-width="1.5"/></svg><div><b>EMAIL ADDRESS</b><span>hello@larkibite.ca</span></div></div>
    <div class="fcontact"><svg width="18" height="18" viewBox="0 0 24 24"><path fill="none" stroke="#fff" stroke-width="1.8" d="M6.6 10.8a15 15 0 0 0 6.6 6.6l2.2-2.2c.3-.3.7-.4 1-.2 1.1.4 2.3.6 3.6.6.6 0 1 .4 1 1V20c0 .6-.4 1-1 1A17 17 0 0 1 3 4c0-.6.4-1 1-1h3.5c.6 0 1 .4 1 1 0 1.3.2 2.5.6 3.6.1.3 0 .7-.2 1z"/></svg><div><b>PHONE NUMBER</b><span>416-555-0142</span></div></div>
  </div>
  <div class="abs fcol" style="left:385px"><h5>ABOUT</h5><ul><li>Home</li><li>About Us</li><li>Services</li><li>Customer Login</li></ul></div>
  <div class="abs fcol" style="left:563px"><h5>RESOURCES</h5><ul><li>Support</li><li>Why Us</li><li>Testimonials</li><li>FAQ</li></ul></div>
  <div class="abs fcol" style="left:790px">
    <h5>QUESTIONS?</h5>
    <span class="field">Your Name</span><span class="field">Email address</span><span class="field">Phone</span>
    <div class="send">SEND</div>
  </div>
  <div class="abs fdivider"></div>
  <div class="abs copy">© 2018 Company Name &nbsp;All right reserved</div>
</footer>

</body>
</html>
```